Lunelle Rosa Hair Fancy Business Card’s

I want my business cards to be elite, original and very classy. I want the business cards to match the colors of my logo and to match the design posted. I would love the design of the picture I posted

I want the card all white .
The dripping on the top of the card I want it to match the pink color in my logo that’s also posted .
I need my logo on the business card !
I need my Instagram- @lunelle.rosa.hair__
And my phone number - 555 207 3962

Target Market(s)

My target market is young woman age 23 to older woman to the age of 65
I want both older and younger women to love my design . I don’t want any cheap looking business cards

Industry/Entity Type

Hair And Beauty

Contact Information for Business Card

Add my logo
Add my Instagram- @lunelle.rosa.hair__
My number - 555 207 3962
My website- www.lunellerosahair.example

Font styles to use
Serif
Script

Colors
ffffff
e667a6
e34298

Requirements
Must have
• The business cards must have my logo, my number , my website, and my Instagram!
Nice to have
• Nice to have glitter words that match my logo
• The business cards must look classy and mature
• I want them to be very unique!!
Should not have
• Should not have any colors that doesn’t match my logo ! This is very important! Please

```html
<!DOCTYPE html>
<html lang="en">
<head>
<meta charset="utf-8">
<title>Lunelle Rosa Hair – Business Card</title>
<link rel="stylesheet" href="https://fonts.googleapis.com/css2?family=Playfair+Display:wght@600&family=Great+Vibes&family=Roboto:wght@400;700&display=swap">
<style>
  :root {
    --stage: #3b3b3b;
    --white: #ffffff;
    --pink: #e667a6;
    --pink-deep: #e34298;
    --pink-pale: #f7bfd7;
  }
  * { margin: 0; padding: 0; box-sizing: border-box; }
  html, body { width: 1200px; height: 1200px; overflow: hidden; }
  body {
    background: var(--stage);
    display: flex;
    flex-direction: column;
    align-items: center;
    justify-content: center;
    gap: 60px;
  }
  .card {
    position: relative;
    width: 840px;
    height: 480px;
    border-radius: 26px;
    overflow: hidden;
  }
  .card--front { background: var(--white); }
  .card--back { background: var(--pink); }

  .brand-name {
    font-family: "Playfair Display", Georgia, serif;
    font-weight: 600;
    white-space: nowrap;
  }
  .card--front .brand-name {
    position: absolute;
    left: 0; right: 0;
    top: 50%;
    transform: translateY(-50%);
    text-align: center;
    font-size: 76px;
    color: var(--pink-deep);
    padding-left: 120px;
  }
  .card--back .brand-name {
    position: absolute;
    right: 70px;
    bottom: 70px;
    font-size: 66px;
    color: var(--pink-pale);
  }

  .contact-block {
    position: absolute;
    left: 70px;
    top: 46px;
    color: var(--white);
    font-family: "Roboto", Arial, sans-serif;
  }
  .owner-name {
    font-family: "Great Vibes", cursive;
    font-size: 48px;
    line-height: 1;
    color: var(--pink-pale);
  }
  .owner-role {
    font-weight: 700;
    font-size: 19px;
    letter-spacing: 0.5px;
    margin-top: 4px;
    margin-bottom: 22px;
  }
  .contact-list { list-style: none; }
  .contact-item {
    display: flex;
    align-items: center;
    gap: 8px;
    font-size: 18px;
    letter-spacing: 0.6px;
    line-height: 1.55;
  }
  .contact-icon { width: 16px; height: 16px; flex: none; }
</style>
</head>
<body>
  <section class="card card--front" aria-label="Card front">
    <p class="brand-name">Lunelle Rosa Hair</p>
  </section>

  <section class="card card--back" aria-label="Card back">
    <div class="contact-block">
      <p class="owner-name">Lunelle Rosa</p>
      <p class="owner-role">Custom Wig Maker</p>
      <ul class="contact-list">
        <li class="contact-item">
          <svg class="contact-icon" viewBox="0 0 16 16" aria-hidden="true">
            <circle cx="8" cy="8" r="8" fill="#ffffff"/>
            <path d="M5.2 3.8l1.4 1.6-.8 1.2c.6 1.3 1.5 2.2 2.8 2.8l1.2-.8 1.6 1.4-.9 1.5C7.6 11.3 4.7 8.4 3.8 5.5z" fill="#e667a6"/>
          </svg>
          555 207 3962
        </li>
        <li class="contact-item">
          <svg class="contact-icon" viewBox="0 0 16 16" aria-hidden="true"><circle cx="8" cy="8" r="8" fill="#ffffff"/></svg>
          @lunelle.rosa.hair__
        </li>
        <li class="contact-item">
          <svg class="contact-icon" viewBox="0 0 16 16" aria-hidden="true"><circle cx="8" cy="8" r="8" fill="#ffffff"/></svg>
          www.lunellerosahair.example
        </li>
      </ul>
    </div>
    <p class="brand-name">Lunelle Rosa Hair</p>
  </section>
</body>
</html>
```